Marla’s Sandwich Corner Grand Opening Door Flyer

1. Project Title
• “Flyer Design for Sandwich Shop Grand Opening”
• Why it’s effective: Direct and to the point, highlighting the purpose of the design.

2. Project Description
• “We’re looking for a professional designer to create a vibrant and modern flyer for our sandwich shop, Marla’s Corner. The flyer should emphasize our handcrafted sandwiches, fresh-baked bread, and house-made meats. As a women & family-owned business, we want this aspect prominently displayed. The flyer should also include our logo, a ‘Grand Opening’ and our website: MarlasCorner.example. We want the design to be clean, bold, and visually appealing to attract customers. We also would like a QR code so they can scan to load of the website to order online, but also list it.
• Why it’s effective: Clear goals, modern style preference, and necessary details outlined.

3. Visual Style
• “Modern, bold, and clean design with bright, appetizing colors. Focus on high-quality imagery of sandwiches, sleek fonts, and an inviting layout.”
• Why it’s effective: Communicates the desired aesthetic and tone.

4. Key Details to Include
• Business Name: Marla’s Sandwich Corner
• Taglines:
“Women & Family Owned”
“Handcrafted Sandwiches Made with Love”
“Fresh Baked Bread”
“House-made Slow Roasted House Specialties”
“Gluten-Friendly”
“Vegan-Friendly”
“7:00am Fresh Daily Grounded Coffee and Breakfast”

• Call-to-Action: “Order Online at MarlasCorner.example”
• Placeholder for the logo.
• Size: 4.25 x 11 (Door Hanger)
• File Format: High-resolution PDF, JPEG, or PNG.
• Print-Ready: Include bleed margins and ensure print clarity.

6. Tone
• Friendly and professional. Highlighting that your business is women-owned adds a unique and personal touch vs deli meat shops. We are a gourmet sandwich shop, with fresh baked bread, house-made meats, with gluten and vegan options. Each sandwich is made with love.

Target Market(s)

Coffee drinkers for morning crowd and sandwiches for lunch

Industry/Entity Type

Sandwich Shop

Colors
EB3D1F
EC4F4E
F09395
F8D3D4
FCEDEE

Requirements
Must have
• See Description
Nice to have
• Use website to get a feel for color theme
Should not have
• NA

```html
<!DOCTYPE html>
<html lang="en">
<head>
<meta charset="utf-8">
<title>Marla’s Sandwich Corner — Grand Opening Door Hanger</title>
<link rel="stylesheet" href="https://fonts.googleapis.com/css2?family=Fraunces:opsz,wght@144,900&family=Rubik:wght@800;900&display=swap">
<style>
  :root {
    --tomato: #eb3d1f;
    --tomato-soft: #f04f2a;
    --coral: #ec4f4e;
    --rose: #f09395;
    --blush: #f5bfd6;
    --blush-light: #f8d3d4;
    --cream: #fcedee;
  }
  * { margin: 0; padding: 0; box-sizing: border-box; }
  html, body { width: 1200px; height: 3300px; overflow: hidden; }
  body { background: var(--blush); font-family: "Rubik", sans-serif; font-weight: 900; }

  .hanger { position: relative; width: 1200px; height: 3300px; overflow: hidden; background: var(--blush); }

  .main-oval {
    position: absolute; left: -420px; top: 695px;
    width: 2040px; height: 2032px; border-radius: 50%;
    background: var(--tomato-soft);
  }

  .headline-box {
    position: absolute; left: 147px; top: 800px; width: 910px; height: 320px;
    background: var(--blush); border-radius: 70px;
    display: flex; align-items: center; justify-content: center;
  }
  .headline {
    font-family: "Fraunces", serif; font-weight: 900; color: var(--tomato-soft);
    font-size: 200px; line-height: 0.76; text-align: center; letter-spacing: -3px;
  }

  .brand-name {
    position: absolute; left: 0; top: 1160px; width: 1200px; text-align: center;
    font-family: "Fraunces", serif; font-weight: 900; color: var(--blush);
    font-size: 260px; line-height: 1; letter-spacing: -4px;
  }
  .brand-sub {
    position: absolute; left: 160px; top: 1432px; width: 880px; height: 86px;
    background: var(--blush); color: var(--tomato-soft);
    font-family: "Rubik", sans-serif; font-weight: 900;
    font-size: 58px; line-height: 86px; letter-spacing: 9px; text-align: center;
  }

  .food-photo {
    position: absolute; left: 250px; top: 1522px; width: 720px; height: 510px;
    border-radius: 50%;
    background: radial-gradient(ellipse at 50% 50%, #f7e6dc 0%, #f3b088 38%, #f48a8f 62%, rgba(240,79,42,0) 75%);
  }

  .feature-list {
    position: absolute; left: 0; top: 2060px; width: 1200px; list-style: none;
    text-align: center; color: var(--cream);
    font-family: "Rubik", sans-serif; font-weight: 900;
    font-size: 39px; line-height: 34px; text-transform: uppercase; letter-spacing: 0.5px;
  }
  .feature-list li { margin-bottom: 25px; }

  .order-pill {
    position: absolute; left: 196px; top: 2767px; width: 800px; height: 103px;
    border-radius: 30px; background: var(--tomato-soft);
    color: var(--blush); font-family: "Rubik", sans-serif; font-weight: 900;
    font-size: 78px; line-height: 103px; text-align: center; letter-spacing: -1px;
  }
  .order-url {
    position: absolute; left: 0; top: 2872px; width: 1200px; text-align: center;
    font-family: "Fraunces", serif; font-weight: 900; color: var(--tomato-soft);
    font-size: 84px; line-height: 1.2; letter-spacing: -1px;
  }

  .footer-band {
    position: absolute; left: -300px; top: 3012px; width: 1800px; height: 900px;
    border-radius: 50%; background: var(--tomato-soft);
  }
  .footer-name {
    position: absolute; left: 0; top: 3150px; width: 1200px; text-align: center;
    font-family: "Rubik", sans-serif; font-weight: 900;
    color: var(--blush); font-size: 40px; line-height: 1; letter-spacing: 4px;
    text-transform: uppercase;
  }
</style>
</head>
<body>
<div class="hanger">
  <div class="main-oval"></div>

  <div class="headline-box">
    <h1 class="headline">Grand<br>Opening</h1>
  </div>

  <div class="brand-name">Marla’s</div>
  <div class="brand-sub">SANDWICH CORNER</div>

  <div class="food-photo" role="img" aria-label="Photo of a sandwich with lettuce, tomato and peppers on a plate beside a cup of coffee, with a yellow sticker"></div>

  <ul class="feature-list">
    <li>• Women &amp; Family Owned •</li>
    <li>• Handcrafted Sandwiches •<br>Made with Love</li>
    <li>• Fresh Baked Bread •</li>
    <li>• House-Made Slow Roasted •<br>House Specialties</li>
    <li>• Gluten-Friendly •</li>
    <li>• Vegan-Friendly •</li>
    <li>• 7:00AM Fresh Daily •<br>Grounded Coffee and Breakfast</li>
  </ul>

  <div class="order-pill">ORDER ONLINE AT</div>
  <div class="order-url">MarlasCorner.example</div>

  <div class="footer-band"></div>
  <div class="footer-name">Marla’s Sandwich Corner</div>
</div>
</body>
</html>
```